International emerging specialist Research and Development Company focused on plant-based medicine

We need a powerpoint design for a new company based in British Columbia, Canada called Tavrel Phytocor. We are focused on developing plant-based medicines. The company is driven by its experience in research and development work in plant genetics, cultivation techniques, natural medicines, biochemistry, agriculture and technologies. Tavrel will research, develop and produce very unique and specific cultivars from the plant kingdom needed for specific ailments in medical patients. We would like to see designs that use our current logo and its colour scheme. The final design should communicate financial safety, growth, and research and development.

```html
<!DOCTYPE html>
<html lang="en">
<head>
<meta charset="utf-8">
<title>Tavrel Phytocor – Content Slide</title>
<link href="https://fonts.googleapis.com/css2?family=Roboto+Condensed:wght@400;700&family=Roboto:wght@400&display=swap" rel="stylesheet">
<style>
  :root {
    --brand-red: #d7161f;
    --canvas-bg: #f2f2f2;
    --footer-grey: #d0d0d0;
    --body-text: #3c3c3c;
    --white: #ffffff;
    --subtitle-ghost: rgba(255, 255, 255, 0.85);
  }
  * { margin: 0; padding: 0; box-sizing: border-box; }
  html, body { width: 1200px; height: 900px; overflow: hidden; }
  body {
    position: relative;
    background: var(--canvas-bg);
    font-family: "Roboto", Arial, sans-serif;
  }
  .slide-header {
    position: absolute; left: 0; top: 0;
    width: 1200px; height: 93px;
    background: var(--brand-red);
  }
  .slide-title {
    position: absolute; left: 30px; top: 13px;
    font-family: "Roboto Condensed", "Arial Narrow", sans-serif;
    font-weight: 400; font-size: 51px; line-height: 64px;
    color: var(--white);
  }
  .brand {
    position: absolute; right: 30px; top: 26px;
    display: flex; align-items: center; gap: 10px;
  }
  .brand-dot {
    width: 14px; height: 14px; border-radius: 50%;
    background: var(--white);
  }
  .brand-name {
    font-family: "Roboto Condensed", "Arial Narrow", sans-serif;
    font-weight: 400; font-size: 34px; line-height: 40px;
    color: var(--white);
  }
  .content-block {
    position: absolute; left: 60px; width: 1090px;
  }
  .block-heading {
    display: flex; align-items: center; gap: 14px;
    font-family: "Roboto Condensed", "Arial Narrow", sans-serif;
    font-weight: 700; font-size: 25px; line-height: 32px;
    color: var(--brand-red);
  }
  .bullet-mark { flex: none; width: 16px; height: 16px; }
  .block-text {
    margin-top: 6px; padding-left: 40px; width: 1090px;
    font-size: 18px; line-height: 30px;
    color: var(--body-text);
  }
  .ghost-subtitle {
    position: absolute; right: 50px; top: 433px;
    text-align: right;
    font-size: 18px; line-height: 30px;
    color: var(--subtitle-ghost);
  }
  .slide-footer {
    position: absolute; left: 0; top: 858px;
    width: 1200px; height: 42px;
    background: var(--footer-grey);
  }
</style>
</head>
<body>
  <header class="slide-header">
    <h1 class="slide-title">Project Title Here</h1>
    <div class="brand">
      <span class="brand-dot"></span>
      <span class="brand-name">Tavrel Phytocor</span>
    </div>
  </header>

  <p class="ghost-subtitle">Subtitle here Subtitle here<br>Subtitle here Subtitle here Subtitle here</p>

  <section class="content-block" style="top:153px">
    <h2 class="block-heading"><svg class="bullet-mark" viewBox="0 0 16 16"><circle cx="8" cy="8" r="6" fill="none" stroke="#d7161f" stroke-width="2"/></svg>Bullet Title Heading Here Bullet Title Heading Here</h2>
    <p class="block-text">Lorem ipsum dolor sit Lorem ipsum dolor sit&nbsp; Lorem ipsum dolor sit Lorem ipsum dolor sit&nbsp; Lorem ipsum dolor sit Lorem ipsum dolor sit&nbsp; Lorem ipsum dolor sit Lorem ipsum dolor sit&nbsp; Lorem ipsum dolor sit Lorem ipsum dolor sit&nbsp; Lorem ipsum dolor sit Lorem ipsum dolor sit&nbsp; Lorem ipsum dolor sit Lorem ipsum dolor sit&nbsp; Lorem ipsum dolor sit Lorem ipsum dolor sit</p>
  </section>

  <section class="content-block" style="top:323px">
    <h2 class="block-heading"><svg class="bullet-mark" viewBox="0 0 16 16"><circle cx="8" cy="8" r="6" fill="none" stroke="#d7161f" stroke-width="2"/></svg>Bullet Title Heading Here Bullet Title Heading Here</h2>
    <p class="block-text">Lorem ipsum dolor sit Lorem ipsum dolor sit&nbsp; Lorem ipsum dolor sit Lorem ipsum dolor sit&nbsp; Lorem ipsum dolor sit Lorem ipsum dolor sit&nbsp; Lorem ipsum dolor sit Lorem ipsum dolor sit&nbsp; Lorem ipsum dolor sit Lorem ipsum dolor sit&nbsp; Lorem ipsum dolor sit Lorem ipsum dolor sit&nbsp; Lorem ipsum dolor sit Lorem ipsum dolor sit&nbsp; Lorem ipsum dolor sit Lorem ipsum dolor sit</p>
  </section>

  <section class="content-block" style="top:501px">
    <h2 class="block-heading"><svg class="bullet-mark" viewBox="0 0 16 16"><circle cx="8" cy="8" r="6" fill="none" stroke="#d7161f" stroke-width="2"/></svg>Bullet Title Heading Here Bullet Title Heading Here</h2>
    <p class="block-text">Lorem ipsum dolor sit Lorem ipsum dolor sit&nbsp; Lorem ipsum dolor sit Lorem ipsum dolor sit&nbsp; Lorem ipsum dolor sit Lorem ipsum dolor sit&nbsp; Lorem ipsum dolor sit Lorem ipsum dolor sit&nbsp; Lorem ipsum dolor sit Lorem ipsum dolor sit&nbsp; Lorem ipsum dolor sit Lorem ipsum dolor sit&nbsp; Lorem ipsum dolor sit Lorem ipsum dolor sit&nbsp; Lorem ipsum dolor sit Lorem ipsum dolor sit</p>
  </section>

  <section class="content-block" style="top:683px">
    <h2 class="block-heading"><svg class="bullet-mark" viewBox="0 0 16 16"><circle cx="8" cy="8" r="6" fill="none" stroke="#d7161f" stroke-width="2"/></svg>Bullet Title Heading Here Bullet Title Heading Here</h2>
    <p class="block-text">Lorem ipsum dolor sit Lorem ipsum dolor sit&nbsp; Lorem ipsum dolor sit Lorem ipsum dolor sit&nbsp; Lorem ipsum dolor sit Lorem ipsum dolor sit&nbsp; Lorem ipsum dolor sit Lorem ipsum dolor sit&nbsp; Lorem ipsum dolor sit Lorem ipsum dolor sit&nbsp; Lorem ipsum dolor sit Lorem ipsum dolor sit&nbsp; Lorem ipsum dolor sit Lorem ipsum dolor sit&nbsp; Lorem ipsum dolor sit Lorem ipsum dolor sit</p>
  </section>

  <footer class="slide-footer"></footer>
</body>
</html>
```